Sports / Entertainment Media Co needs a biz card design

We are a media co / luxury lifestyle brand that targets professional athletes, entertainers and high net-worth fans. We are currently preparing for a relaunch and in need for new biz cards. I envision a black on black card with a pop of color on opposite side. Color Palette black, white, red etc. I want this card to exude sexiness and power. Very high stylized, hip and cool. I have attached the logo - I would like to see it all in black, but also open to other ideas. I will also upload a current card with all information needed on this new card. Furthermore I will add some samples of other cards I love. Thanks!!!
Updates

I provided suggestions, however I am open to all ideas!!   Be as creative as you can.  Think cutting-edge, sexy and powerful.  Take a look at the cards I uploaded to get a sense for what I like.  Thanks!!!

Industry/Entity Type

Entertainment

```html
<!DOCTYPE html>
<html lang="en">
<head>
<meta charset="utf-8">
<title>Pulse Business Cards</title>
<link rel="stylesheet" href="https://fonts.googleapis.com/css2?family=Open+Sans:wght@400;600;700&display=swap">
<style>
  :root {
    --backdrop: #9b9b9b;
    --card-white: #ffffff;
    --card-shade: #e9e9e9;
    --band-black: #0a0a0a;
    --ink-dark: #3a3a3a;
    --ink-mid: #555555;
    --accent-red: #e3231b;
    --band-text: #f2f2f2;
  }
  * { box-sizing: border-box; margin: 0; padding: 0; }
  html, body { width: 1200px; height: 933px; overflow: hidden; }
  body {
    background: var(--backdrop);
    font-family: "Open Sans", Arial, sans-serif;
    position: relative;
  }
  .card {
    position: absolute;
    width: 640px;
    height: 366px;
    background: linear-gradient(135deg, var(--card-white) 0%, var(--card-white) 45%, var(--card-shade) 100%);
    box-shadow: 0 14px 30px rgba(0,0,0,0.28);
    overflow: hidden;
  }
  .card--front { left: 440px; top: 80px; }
  .card--back { left: 160px; top: 480px; }

  .card__band {
    position: absolute;
    left: 0; right: 0; bottom: 0;
    height: 62px;
    background: var(--band-black);
    display: flex;
    align-items: center;
    justify-content: center;
  }
  .card__url {
    color: var(--band-text);
    font-size: 15px;
    font-weight: 600;
    letter-spacing: 5px;
  }

  .brand {
    position: absolute;
    display: flex;
    align-items: center;
    gap: 10px;
  }
  .brand__name {
    font-size: 64px;
    font-weight: 700;
    color: var(--band-black);
    letter-spacing: -1px;
    line-height: 1;
  }
  .brand__dot {
    width: 22px;
    height: 22px;
    border-radius: 50%;
    background: var(--accent-red);
  }
  .card--front .brand { left: 190px; top: 110px; }
  .card--back .brand { left: 360px; top: 70px; }
  .card--back .brand__name { font-size: 54px; }
  .card--back .brand__dot { width: 18px; height: 18px; }

  .person { position: absolute; left: 56px; top: 98px; }
  .person__name {
    font-size: 21px;
    font-weight: 700;
    color: var(--ink-dark);
    letter-spacing: 0.5px;
  }
  .person__role {
    font-size: 16px;
    color: var(--ink-mid);
    letter-spacing: 0.5px;
    margin-top: -2px;
  }
  .contact-list {
    position: absolute;
    left: 56px;
    top: 168px;
    list-style: none;
  }
  .contact-list__item {
    display: flex;
    align-items: center;
    gap: 10px;
    font-size: 12px;
    color: var(--ink-mid);
    height: 22px;
  }
  .contact-list__icon {
    width: 17px;
    height: 17px;
    flex: none;
  }
</style>
</head>
<body>

<section class="card card--front">
  <div class="brand">
    <span class="brand__name">pulse</span>
    <span class="brand__dot"></span>
  </div>
  <div class="card__band"><span class="card__url">www.pulsemediahouse.com</span></div>
</section>

<section class="card card--back">
  <div class="person">
    <p class="person__name">MARCUS VALE</p>
    <p class="person__role">GENERAL MANAGER</p>
  </div>
  <ul class="contact-list">
    <li class="contact-list__item">
      <svg class="contact-list__icon" viewBox="0 0 17 17" aria-hidden="true">
        <rect width="17" height="17" fill="var(--accent-red)"/>
        <path d="M8.5 3.5a3 3 0 0 1 3 3c0 2.2-3 6-3 6s-3-3.8-3-6a3 3 0 0 1 3-3z" fill="#fff"/>
        <circle cx="8.5" cy="6.5" r="1.1" fill="var(--accent-red)"/>
      </svg>
      <span>42 Harbor Lane, Suite 7, Westfield</span>
    </li>
    <li class="contact-list__item">
      <svg class="contact-list__icon" viewBox="0 0 17 17" aria-hidden="true">
        <rect width="17" height="17" fill="var(--accent-red)"/>
        <path d="M5 4h2l1 2.5-1.2.9a6 6 0 0 0 2.8 2.8l.9-1.2L13 10v2a1 1 0 0 1-1 1A8 8 0 0 1 4 5a1 1 0 0 1 1-1z" fill="#fff"/>
      </svg>
      <span>555 210 4836</span>
    </li>
    <li class="contact-list__item">
      <svg class="contact-list__icon" viewBox="0 0 17 17" aria-hidden="true">
        <rect width="17" height="17" fill="var(--accent-red)"/>
        <rect x="3.5" y="5" width="10" height="7" fill="#fff"/>
        <path d="M3.5 5l5 4 5-4" fill="none" stroke="var(--accent-red)" stroke-width="1"/>
      </svg>
      <span>marcus@pulsemedia.com</span>
    </li>
  </ul>
  <div class="brand">
    <span class="brand__name">pulse</span>
    <span class="brand__dot"></span>
  </div>
  <div class="card__band"><span class="card__url">www.pulsemediahouse.com</span></div>
</section>

</body>
</html>
```